Web Design Project - brivolta

I'm building an agency for marketing solutions but also medical education and patients education for pharmaceutical companies, medical societies and patient advocacy groups. We want to be perceived as the most innovative in the market. We work through design thinking solutions for campaigns and services.
I love some websites based on Swiss style design like www.quorlinex.com
We are a small group of designers, physicians and creatives working together to deliver the best experiences in our market.
We decided to also use pixel bazaar expecting that we maybe found a great idea we didn't thought about yet.

I'm extending it for more 2 weeks

Reason: I need the best design you can. Only PSD. No code needed. Love Swiss style, like velmora 5 and quorlinex.com I'm extending the deadline until get something great. Willing to extend as much as needed.

Target Market(s)

Pharmaceutical companies, physicians, medical societies, patients advocacy groups

Industry/Entity Type

Pharmaceutical

Font styles to use
Other font styles liked:
• Helvetia family

Colors

Designer to choose colors to be used in the design.

Requirements
Must have
• Must be innovative like www.quorlinex.com
Nice to have
• Cool menus
Should not have
• Not to appear too much Comercial. We like to be a boutique in this market. Craftsmen working with less clients at time but delivering precious stones.

```html
<!DOCTYPE html>
<html lang="en">
<head>
<meta charset="utf-8">
<title>brivolta — home</title>
<link rel="stylesheet" href="https://fonts.googleapis.com/css2?family=Arimo:wght@400;700&family=Source+Sans+3:wght@300;600&display=swap">
<style>
  :root {
    --sky: #c4effd;
    --cyan: #00c5f2;
    --orange: #ff6a00;
    --ink: #111111;
    --white: #ffffff;
    --rule: #ffffff;
    --icon: #1a1a1a;
    --caption-light: rgba(255,255,255,0.85);
    --caption-dark: rgba(40,40,40,0.72);
  }
  * { box-sizing: border-box; margin: 0; padding: 0; }
  html, body { width: 1190px; height: 1200px; overflow: hidden; }
  body {
    background: var(--sky);
    font-family: "Arimo", Helvetica, Arial, sans-serif;
    color: var(--ink);
    position: relative;
  }
  .site-header { position: absolute; left: 92px; top: 0; width: 1007px; height: 98px; }
  .brand {
    position: absolute; left: 2px; top: 47px;
    font-size: 31px; font-weight: 400; color: var(--ink); letter-spacing: -0.3px;
  }
  .header-rule { position: absolute; left: 0; top: 93px; width: 1007px; height: 4px; background: var(--rule); }
  .main-nav { position: absolute; left: 0; top: 0; }
  .nav-item { position: absolute; top: 40px; width: 50px; height: 46px; display: flex; align-items: center; justify-content: center; }
  .nav-item.is-active::after {
    content: ""; position: absolute; left: -4px; right: -4px; top: 53px; height: 4px; background: var(--orange);
  }
  .nav-sep { position: absolute; top: 40px; width: 1px; height: 46px; background: #9fdcee; }
  .contact-button {
    position: absolute; left: 948px; top: 39px; width: 59px; height: 48px;
    background: var(--orange); display: flex; align-items: center; justify-content: center;
  }

  .tile { position: absolute; overflow: hidden; }
  .photo { position: absolute; inset: 0; }

  .welcome { left: 92px; top: 141px; width: 471px; height: 437px; background: var(--cyan); padding: 24px 26px 0 25px; }
  .welcome h1 { font-weight: 400; color: var(--white); font-size: 40px; letter-spacing: -0.8px; line-height: 1; white-space: nowrap; }
  .welcome h1 strong { font-weight: 400; color: var(--ink); font-size: 51px; letter-spacing: -0.5px; }
  .welcome p {
    margin-top: 19px; font-family: "Source Sans 3", Helvetica, sans-serif; font-weight: 300;
    font-size: 31px; line-height: 42px; letter-spacing: 1.4px; color: var(--white); padding-left: 3px;
  }
  .welcome p b { font-weight: 600; }

  .feature { left: 604px; top: 141px; width: 493px; height: 437px; }
  .feature .photo { background: linear-gradient(135deg, #d9d3cc 0%, #bfc6cc 35%, #7fb8dc 55%, #5a6470 80%, #2e3338 100%); }
  .caption-dark {
    position: absolute; left: 0; right: 0; bottom: 0; height: 64px; background: var(--caption-dark);
    color: var(--white); font-size: 49px; font-weight: 400; padding-left: 28px; line-height: 64px; letter-spacing: 0.4px;
  }

  .card { top: 624px; width: 309px; height: 243px; }
  .card-a { left: 92px; }
  .card-b { left: 441px; }
  .card-a .photo { background: linear-gradient(160deg, #6b5a4c 0%, #d8cfc6 40%, #e9e7e4 60%, #1d2a48 100%); }
  .card-b .photo { background: linear-gradient(135deg, #e6f0f8 0%, #b5cde6 40%, #3b68b8 70%, #c9d9ef 100%); }
  .people .photo { background: linear-gradient(120deg, #c7d9c4 0%, #e9e6df 40%, #a77b5a 65%, #5c8fc6 100%); }
  .caption-light {
    position: absolute; left: 0; right: 0; bottom: 0; height: 50px; background: var(--caption-light);
    font-weight: 700; font-size: 26px; line-height: 52px; text-align: center; letter-spacing: 0.6px; color: var(--ink);
  }
  .societies { left: 789px; top: 624px; width: 309px; height: 243px; background: var(--orange); padding: 22px 14px 0 14px; }
  .societies h2 { font-weight: 400; font-size: 31px; color: var(--white); letter-spacing: -0.4px; white-space: nowrap; }
  .societies h2 strong { font-weight: 400; color: var(--ink); font-size: 37px; }
  .societies p { margin-top: 14px; font-size: 20px; line-height: 27.5px; letter-spacing: 0.9px; color: var(--white); padding-left: 2px; }

  .people { left: 92px; top: 912px; width: 309px; height: 244px; }

  .contact { left: 441px; top: 912px; width: 657px; height: 244px; background: var(--cyan); padding: 14px 16px 0 16px; color: var(--white); }
  .contact h2 { font-weight: 400; font-size: 53px; letter-spacing: 0.2px; line-height: 1.1; }
  .contact ul { list-style: none; margin-top: 13px; }
  .contact li { display: flex; align-items: center; font-size: 21px; height: 40px; letter-spacing: 0.2px; }
  .contact li svg { width: 16px; margin-right: 15px; flex: none; }
  .contact li.legal { font-size: 16.5px; height: 34px; margin-top: 2px; }
</style>
</head>
<body>
  <header class="site-header">
    <div class="brand">brivolta</div>
    <nav class="main-nav" aria-label="Main">
      <a class="nav-item is-active" style="left:206px" aria-label="Home">
        <svg width="44" height="42" viewBox="0 0 44 42" fill="none" stroke="#1a1a1a" stroke-width="2.4" stroke-linejoin="round"><path d="M3 20 L22 3 L41 20"/><path d="M31 11 V4 H36 V15"/><path d="M8 16 V39 H18 V27 H26 V39 H36 V16"/></svg>
      </a>
      <span class="nav-sep" style="left:290px"></span>
      <a class="nav-item" style="left:324px" aria-label="Services">
        <svg width="40" height="38" viewBox="0 0 40 38" fill="none" stroke="#1a1a1a" stroke-width="2.4" stroke-linejoin="round"><rect x="2" y="8" width="36" height="28" rx="3"/><path d="M14 8 V3 H26 V8"/><path d="M20 15 V29 M13 22 H27" stroke-width="3"/></svg>
      </a>
      <span class="nav-sep" style="left:410px"></span>
      <a class="nav-item" style="left:443px" aria-label="Ideas">
        <svg width="46" height="42" viewBox="0 0 46 42" fill="none" stroke="#1a1a1a" stroke-width="2"><path d="M23 8 a10 10 0 0 1 6 18 v6 h-12 v-6 a10 10 0 0 1 6 -18z"/><path d="M18 35 h10 M19 38 h8"/><path d="M23 1 v4 M9 7 l3 3 M37 7 l-3 3 M3 19 h5 M38 19 h5 M8 29 l3 -2 M38 29 l-3 -2"/></svg>
      </a>
      <span class="nav-sep" style="left:528px"></span>
      <a class="nav-item" style="left:556px" aria-label="Pharma">
        <svg width="30" height="44" viewBox="0 0 30 44" fill="none" stroke="#1a1a1a" stroke-width="2.2" stroke-linejoin="round"><rect x="8" y="2" width="14" height="5"/><path d="M8 7 V11 L3 16 V41 H27 V16 L22 11 V7"/><path d="M15 23 V33 M10 28 H20"/><path d="M8 11 H22"/></svg>
      </a>
    </nav>
    <a class="contact-button" aria-label="Contact">
      <svg width="46" height="34" viewBox="0 0 46 34" fill="none" stroke="#ffffff" stroke-width="2.4"><rect x="2" y="2" width="42" height="28" rx="4"/><circle cx="15" cy="12" r="4"/><path d="M7 24 c1 -6 15 -6 16 0"/><circle cx="33" cy="13" r="3"/><path d="M36 13 v2 a2 2 0 0 0 3 0 v-2 a6 6 0 1 0 -3 5"/><path d="M10 30 v3 M36 30 v3"/></svg>
    </a>
    <div class="header-rule"></div>
  </header>

  <section class="tile welcome">
    <h1>welcome to <strong>brivolta</strong></h1>
    <p>simply dummy text of the printing and typesetting in-dustry. <b>Lorem Ipsum</b> has been the industry's standard dummy text ever since the 1500s, when an unknown printer took a galley.</p>
  </section>

  <section class="tile feature">
    <div class="photo" role="img" aria-label="Photo of a man typing on a laptop showing a surgical procedure"></div>
    <div class="caption-dark">Medical Education</div>
  </section>

  <section class="tile card card-a">
    <div class="photo" role="img" aria-label="Photo of two colleagues reviewing documents at a table with coffee"></div>
    <div class="caption-light">Marketing Solutions</div>
  </section>

  <section class="tile card card-b">
    <div class="photo" role="img" aria-label="Photo of white pills and capsules with a blue grid overlay"></div>
    <div class="caption-light">Pharmaceutical</div>
  </section>

  <section class="tile societies">
    <h2>medical <strong>societies</strong></h2>
    <p>Lorem Ipsum has been the industry's standard dummy text ever since the 1500s, when an unknown printer</p>
  </section>

  <section class="tile people">
    <div class="photo" role="img" aria-label="Photo of smiling students seated in a classroom"></div>
    <div class="caption-light">Medical Education</div>
  </section>

  <section class="tile contact">
    <h2>brivolta</h2>
    <ul>
      <li><svg viewBox="0 0 16 16" fill="#111"><path d="M3 1 L6 1 L7 5 L5 6.5 C6 9 7 10 9.5 11 L11 9 L15 10 L15 13 C15 14 14 15 13 15 C6 14 2 10 1 3 C1 2 2 1 3 1Z"/></svg>+44 1632 960418</li>
      <li><svg viewBox="0 0 16 16" fill="#111"><path d="M1 4 H15 V13 H1Z" /><path d="M1 4 L8 9 L15 4" stroke="#00c5f2" stroke-width="1.3" fill="none"/></svg>hello@brivolta.com</li>
      <li><svg viewBox="0 0 16 16" fill="#111"><rect x="7" y="1" width="2" height="14"/><path d="M9 3 H15 L13 5 L15 7 H9Z"/><path d="M7 6 H2 L1 7.5 L2 9 H7Z"/></svg>27 Larkmoor Row, Fenwick, FW2 8LT, USA</li>
      <li class="legal"><svg viewBox="0 0 16 16" fill="none" stroke="#111" stroke-width="1.6"><circle cx="8" cy="8" r="6.5"/><path d="M10.5 6 A3 3 0 1 0 10.5 10"/></svg>2014 brivolta. All Rights Reserved | Privacy Policy</li>
    </ul>
  </section>
</body>
</html>
```